Brindlewick Solutions Ltd

I'd like to create a company letterhead for the attached logo in word format.

I'd like to emphasis the icon in large translucent state from the left corner and ensure that the letterhead colouring matches the colour palette of the current logo with a contrast so it's clear to see. I've attached a copy of our sister company page on the app for reference.

```html
<!DOCTYPE html>
<html lang="en">
<head>
<meta charset="utf-8">
<title>Brindlewick Solutions Ltd — Letterhead</title>
<link href="https://fonts.googleapis.com/css2?family=Lato:wght@400;700&display=swap" rel="stylesheet">
<style>
  :root {
    --teal: #00b9a5;
    --teal-soft: rgba(0, 185, 165, 0.16);
    --ink: #3a3a3a;
    --paper: #ffffff;
    --backdrop: #e9ebea;
  }
  * { box-sizing: border-box; margin: 0; padding: 0; }
  html, body {
    width: 1061px; height: 1200px; overflow: hidden;
    background: var(--backdrop);
    font-family: "Lato", Arial, sans-serif;
  }
  .letterhead {
    position: absolute; left: 127px; top: 30px;
    width: 806px; height: 1140px;
    background: var(--paper);
    box-shadow: 0 4px 18px rgba(0,0,0,0.18);
    overflow: hidden;
  }
  .corner-glow {
    position: absolute; left: 0; top: 0;
    width: 330px; height: 340px;
    background: radial-gradient(circle at 90px 98px, var(--teal-soft) 0, rgba(0,185,165,0.10) 90px, rgba(0,185,165,0) 300px);
  }
  .brand {
    position: absolute; left: 38px; top: 76px;
    display: flex; align-items: center; gap: 10px;
  }
  .brand-dot {
    width: 34px; height: 34px; border-radius: 50%;
    background: var(--teal);
  }
  .brand-name {
    font-size: 27px; font-weight: 400; color: var(--teal);
    letter-spacing: 0.2px;
  }
  .divider {
    position: absolute; top: 67px; width: 1px; height: 57px;
    background: var(--teal);
  }
  .divider--address { left: 314px; }
  .divider--contact { left: 522px; }
  .address {
    position: absolute; left: 347px; top: 70px;
    font-size: 13px; line-height: 18px; color: var(--ink);
    font-style: normal;
  }
  .address .company { color: var(--teal); font-weight: 700; }
  .contact {
    position: absolute; left: 551px; top: 70px;
    list-style: none; font-size: 13px; line-height: 18px; color: var(--ink);
  }
  .contact li { display: flex; align-items: center; gap: 7px; }
  .contact svg { width: 12px; height: 12px; fill: var(--teal); flex: none; }
  .footer-band {
    position: absolute; left: 0; bottom: 0;
    width: 100%; height: 57px;
    background: var(--teal);
    display: flex; align-items: center; justify-content: center;
  }
  .footer-band .web {
    color: #ffffff; font-size: 12px; letter-spacing: 3.2px;
  }
  .footer-band .web b { font-weight: 700; }
</style>
</head>
<body>
  <main class="letterhead">
    <div class="corner-glow" role="img" aria-label="Large faint teal sunburst emblem radiating from the top left corner"></div>

    <div class="brand">
      <span class="brand-dot"></span>
      <span class="brand-name">Brindlewick</span>
    </div>

    <span class="divider divider--address"></span>
    <address class="address">
      <div class="company">Brindlewick Solutions Ltd</div>
      <div>4380 Fernhollow Lane</div>
      <div>Ashbury, CT 06742</div>
    </address>

    <span class="divider divider--contact"></span>
    <ul class="contact">
      <li>
        <svg viewBox="0 0 24 24" aria-hidden="true"><path d="M6.6 10.8c1.4 2.8 3.8 5.1 6.6 6.6l2.2-2.2c.3-.3.7-.4 1-.2 1.1.4 2.3.6 3.6.6.6 0 1 .4 1 1V20c0 .6-.4 1-1 1C10.6 21 3 13.4 3 4c0-.6.4-1 1-1h3.5c.6 0 1 .4 1 1 0 1.3.2 2.5.6 3.6.1.3 0 .7-.2 1z"/></svg>
        (555) 218-4470
      </li>
      <li>
        <svg viewBox="0 0 24 24" aria-hidden="true"><path d="M6 2h12v6H6zM3 9h18a1 1 0 0 1 1 1v7h-4v5H6v-5H2v-7a1 1 0 0 1 1-1zm5 7v4h8v-4z"/></svg>
        (555) 218-4471
      </li>
      <li>
        <svg viewBox="0 0 24 24" aria-hidden="true"><path d="M2 5h20v14H2zm2 2v.5l8 5 8-5V7l-8 5z"/></svg>
        info@brindlewicksolutions.com
      </li>
    </ul>

    <footer class="footer-band">
      <span class="web">www.<b>BrindlewickSolutions</b>.com</span>
    </footer>
  </main>
</body>
</html>
```